Need webdesign for service company that provides Car hiring service and transit service

We need a web design for a company that provides airport transit services and transport services including Limo, Corporate cars, Disability transit, Family transit service. We need is a simple and professional design.

Below is site which we like and also offer the same service http://www.ridelarkway.com.au/
Updates

Project Deadline Extended
Reason: Waiting for the Feedback from multiple stakeholders. Need the time to select and approve the design

Target Market(s)

Tourism, Travel

Industry/Entity Type

Airport

Number of Pages Required

3 page

Font styles to use
Decorative
Script

Requirements
Must have
• Simple and Professional, Site we like http://www.ridelarkway.com.au/ and also need to mobile friendly
Should not have
• Shouldn't have too many images

```html
<!DOCTYPE html>
<html lang="en">
<head>
<meta charset="utf-8">
<title>Ridewell – Private &amp; Business Transport</title>
<link href="https://fonts.googleapis.com/css2?family=Nunito+Sans:wght@300;400;600;800;900&family=Open+Sans:ital,wght@0,400;0,600;0,700;1,400&display=swap" rel="stylesheet">
<style>
:root{
  --ink:#ffffff;
  --ink-soft:#e6e6e6;
  --bg-dark:#2b2d31;
  --bg-mid:#4a4d52;
  --rule:rgba(255,255,255,.45);
  --panel:rgba(110,110,112,.78);
  --field:#ffffff;
  --field-text:#9a9a9a;
  --accent:#e8762c;
  --tile-corporate:#e2636c;
  --tile-limo:#6cb933;
  --tile-family:#e18a3b;
  --tile-disability:#4ba4e2;
  --card-face:#f1f1f1;
}
*{box-sizing:border-box;margin:0;padding:0}
html,body{width:1186px;height:1200px;overflow:hidden}
body{position:relative;font-family:"Open Sans",sans-serif;color:var(--ink);background:var(--bg-dark)}
.backdrop{position:absolute;inset:0;background:
  radial-gradient(ellipse at 30% 55%,rgba(120,125,130,.55),transparent 60%),
  linear-gradient(180deg,#55585c 0%,#3d4044 45%,#2a2c2f 75%,#1f2023 100%)}
.site-header{position:absolute;left:0;top:0;width:1186px;height:93px;border-bottom:1px solid var(--rule)}
.brand{position:absolute;left:97px;top:26px;display:flex;align-items:center;gap:12px}
.brand-mark{width:34px;height:34px;border:2px solid var(--ink)}
.brand-name{font-family:"Nunito Sans",sans-serif;font-weight:800;font-size:30px;letter-spacing:1px}
.search{position:absolute;left:740px;top:28px;width:217px;height:30px;border-bottom:1px solid var(--ink-soft);font-size:13px;padding-top:4px}
.search svg{position:absolute;right:6px;top:4px}
.round-btn{position:absolute;top:25px;width:41px;height:41px;border:1.5px solid var(--ink);border-radius:50%;display:flex;align-items:center;justify-content:center}
.hero-title{position:absolute;left:0;width:1186px;top:140px;text-align:center;font-family:"Nunito Sans",sans-serif;font-weight:300;font-size:51px;letter-spacing:.5px}
.hero-title b{font-weight:900}
.hero-sub{position:absolute;left:0;width:1186px;top:208px;text-align:center;font-family:"Nunito Sans",sans-serif;font-size:24px;font-weight:400}
.hero-text{position:absolute;left:250px;width:686px;top:261px;text-align:center;font-size:14.5px;line-height:27px}
.quote{position:absolute;left:97px;top:362px;width:384px;height:407px;background:var(--panel)}
.quote h2{position:absolute;left:22px;top:20px;font-family:"Nunito Sans",sans-serif;font-weight:300;font-size:27px;width:338px;padding-bottom:14px;border-bottom:3px double rgba(255,255,255,.6)}
.quote h2 b{font-weight:900}
.field{position:absolute;left:24px;width:339px;height:45px;background:var(--field);display:flex;align-items:center;font-size:12.5px;color:var(--field-text)}
.field .ico{width:36px;height:33px;border-right:1px solid #ddd;display:flex;align-items:center;justify-content:center;margin-right:16px}
.opt{position:absolute;left:24px;font-size:14px;display:flex;align-items:center;gap:12px}
.estimate{position:absolute;left:24px;top:303px;width:194px;height:46px;border-radius:23px;background:var(--accent);border:2px solid #fff;font-weight:700;font-size:16px;display:flex;align-items:center;justify-content:center}
.note{position:absolute;left:24px;top:366px;font-size:13px;font-style:italic}
.tile{position:absolute;display:flex;align-items:flex-end;padding:0 0 31px 30px;font-family:"Nunito Sans",sans-serif;font-weight:300;font-size:25px;letter-spacing:.3px}
.tile b{font-weight:900}
.t-corporate{left:501px;top:362px;width:347px;height:194px;background:linear-gradient(135deg,#e8717a,var(--tile-corporate) 60%,#cf535e)}
.t-limo{left:867px;top:362px;width:221px;height:194px;background:linear-gradient(135deg,#7fc740,var(--tile-limo) 60%,#5aa12a)}
.t-family{left:501px;top:576px;width:221px;height:193px;background:linear-gradient(135deg,#e99a50,var(--tile-family) 60%,#cd7a2f);padding-left:18px}
.t-disability{left:741px;top:576px;width:347px;height:193px;background:linear-gradient(135deg,#66b3e8,var(--tile-disability) 60%,#3a93d3);padding-left:29px}
.band{position:absolute;left:0;width:1186px;border-top:1px solid var(--rule)}
.feature{position:absolute;top:880px;width:240px;margin-left:-120px;text-align:center}
.feature svg{display:block;margin:0 auto;height:54px}
.feature h3{margin-top:28px;font-family:"Nunito Sans",sans-serif;font-weight:600;font-size:19px}
.feature p{margin-top:12px;font-size:13px;line-height:20px}
.feature a{display:block;margin-top:14px;font-weight:700;font-size:14px;color:var(--ink);text-decoration:none}
.copyright{position:absolute;left:99px;top:1145px;font-size:13px}
.cards{position:absolute;left:872px;top:1142px;display:flex;gap:6px}
.cards span{width:39px;height:24px;border-radius:3px;background:var(--card-face)}
</style>
</head>
<body>
<div class="backdrop" role="img" aria-label="Background photo of travellers with luggage walking from a private jet to a waiting limousine on an airfield"></div>

<header class="site-header">
  <div class="brand"><span class="brand-mark"></span><span class="brand-name">RIDEWELL</span></div>
  <div class="search">Search
    <svg width="18" height="18" viewBox="0 0 18 18"><circle cx="7.5" cy="7.5" r="5.5" fill="none" stroke="#fff" stroke-width="2.2"/><line x1="11.5" y1="11.5" x2="16" y2="16" stroke="#fff" stroke-width="2.6" stroke-linecap="round"/></svg>
  </div>
  <div class="round-btn" style="left:987px">
    <svg width="18" height="16" viewBox="0 0 18 16"><rect y="1" width="18" height="2.6" rx="1.3" fill="#fff"/><rect y="6.7" width="18" height="2.6" rx="1.3" fill="#fff"/><rect y="12.4" width="18" height="2.6" rx="1.3" fill="#fff"/></svg>
  </div>
  <div class="round-btn" style="left:1046px">
    <svg width="16" height="16" viewBox="0 0 24 24"><path fill="#fff" d="M6.6 10.8a15.1 15.1 0 0 0 6.6 6.6l2.2-2.2a1 1 0 0 1 1-.25 11.4 11.4 0 0 0 3.6.57 1 1 0 0 1 1 1V20a1 1 0 0 1-1 1A17 17 0 0 1 3 4a1 1 0 0 1 1-1h3.5a1 1 0 0 1 1 1c0 1.25.2 2.45.57 3.57a1 1 0 0 1-.25 1z"/></svg>
  </div>
</header>

<h1 class="hero-title">PRIVATE &amp; <b>BUSINESS</b></h1>
<p class="hero-sub">Personalised Transport Services</p>
<p class="hero-text">Nemo enim ipsam voluptatem quia voluptas sit aspernatur aut odit aut fugit, sed quia consequ untur magni dolores eos qui ratione voluptatem sequi nesciu orro quisqu</p>

<section class="quote">
  <h2>GET <b>INSTANT QUOTE</b></h2>
  <div class="field" style="top:96px"><span class="ico"><svg width="18" height="18" viewBox="0 0 18 18"><circle cx="9" cy="9" r="8.5" fill="#a8a8a8"/><path d="M4 6c2 0 3 1 3 3s2 2 2 4M11 3c0 2 2 2 3 3" stroke="#fff" stroke-width="1.4" fill="none"/></svg></span>Origin (Public Location or Exact Address)</div>
  <div class="field" style="top:159px"><span class="ico"><svg width="12" height="18" viewBox="0 0 12 18"><path d="M6 0a6 6 0 0 0-6 6c0 4.5 6 12 6 12s6-7.5 6-12a6 6 0 0 0-6-6z" fill="#a8a8a8"/><circle cx="6" cy="6" r="2.2" fill="#fff"/></svg></span>Destination (Public Location or Exact Address)</div>
  <div class="opt" style="top:231px"><svg width="13" height="13" viewBox="0 0 13 13"><rect x="5" width="3" height="13" fill="#fff"/><rect y="5" width="13" height="3" fill="#fff"/></svg>Add Stops</div>
  <div class="opt" style="top:262px"><svg width="13" height="13" viewBox="0 0 13 13"><circle cx="6.5" cy="6.5" r="5.5" fill="none" stroke="#fff" stroke-width="1.8"/><circle cx="6.5" cy="6.5" r="2.4" fill="#fff"/></svg>Show other vehicles</div>
  <div class="estimate">ESTIMATE FARE</div>
  <p class="note">*See price guide for extras</p>
</section>

<div class="tile t-corporate" role="img" aria-label="Photo of a chauffeur in a suit beside a car and private jet"><span>CORPORATE <b>CARS</b></span></div>
<div class="tile t-limo" role="img" aria-label="Photo of a couple with luggage walking to a limousine"><span>LIMO <b>TRANSIT</b></span></div>
<div class="tile t-family" role="img" aria-label="Photo of a family riding in a convertible"><span>FAMILY <b>TRANSIT</b></span></div>
<div class="tile t-disability" role="img" aria-label="Photo of a passenger in a wheelchair being helped into a car"><span>DISABILITY <b>TRANSIT</b></span></div>

<div class="band" style="top:833px"></div>

<div class="feature" style="left:201px">
  <svg viewBox="0 0 56 40" width="56"><rect x="6" y="2" width="44" height="28" rx="2" fill="none" stroke="#fff" stroke-width="3.5"/><rect x="0" y="33" width="56" height="4" rx="2" fill="#fff"/></svg>
  <h3>Real time booking</h3>
  <p>Nemo enim ipsam voluptatem quia vol uptas sit aspernatur aut od</p>
  <a href="#">BOOK NOW!</a>
</div>
<div class="feature" style="left:460px">
  <svg viewBox="0 0 56 52" width="56"><circle cx="13" cy="10" r="7" fill="#fff"/><circle cx="43" cy="10" r="7" fill="#fff"/><circle cx="28" cy="16" r="9" fill="#fff"/><path d="M0 34c0-8 5-13 13-13s10 4 10 4l-4 12H0z" fill="#fff"/><path d="M56 34c0-8-5-13-13-13s-10 4-10 4l4 12h19z" fill="#fff"/><path d="M10 52V42c0-10 8-15 18-15s18 5 18 15v10z" fill="#fff"/></svg>
  <h3>Become a Member</h3>
  <p>Nemo enim ipsam voluptatem quia vol uptas sit aspernatur aut od</p>
  <a href="#">JOIN US NOW!</a>
</div>
<div class="feature" style="left:722px">
  <svg viewBox="0 0 56 44" width="56"><rect x="2" y="2" width="52" height="40" rx="3" fill="none" stroke="#fff" stroke-width="3.5"/><rect x="2" y="11" width="52" height="7" fill="#fff"/><rect x="10" y="31" width="8" height="3" fill="#fff"/><rect x="21" y="31" width="8" height="3" fill="#fff"/></svg>
  <h3>Secure Online Payment</h3>
  <p>Nemo enim ipsam voluptatem quia vol uptas sit aspernatur aut od</p>
  <a href="#">PAY NOW!</a>
</div>
<div class="feature" style="left:982px">
  <svg viewBox="0 0 60 48" width="60"><path d="M14 4h32l6 16H8z" fill="#fff"/><path d="M19 8h22l3.5 10h-29z" fill="#2f3135"/><rect x="0" y="18" width="60" height="20" rx="8" fill="#fff"/><circle cx="12" cy="28" r="4" fill="#2f3135"/><circle cx="48" cy="28" r="4" fill="#2f3135"/><rect x="6" y="36" width="10" height="11" rx="3" fill="#fff"/><rect x="44" y="36" width="10" height="11" rx="3" fill="#fff"/></svg>
  <h3>Become a Driver</h3>
  <p>Nemo enim ipsam voluptatem quia vol uptas sit aspernatur aut od</p>
  <a href="#">CONTACT US!</a>
</div>

<div class="band" style="top:1110px"></div>
<footer>
  <p class="copyright">© Copyright 2017 - Ridewell. All rights reserved.</p>
  <div class="cards" aria-label="Accepted payment methods"><span></span><span></span><span></span><span></span><span></span></div>
</footer>
</body>
</html>
```